Wealth management Facebook Advertisement

Hello, we are trying to capture more leads to our online booking link through Facebook advertisement. We want an attractive modern design to get more clients and catch the attention of high net-worth clients. We deal with high-net-worth retirees, business owners, farmers, and wealth transfer. We offer high-net-worth client solutions that cover Financial Planning, Retirement and Estate Planning, Investment Planning, Tax Planning, and Insurance Planning. The final design that we would be looking for is modern and eye-catching and makes the prospective clients want to click our meeting link to schedule an introductory consultation.

We are in the Wealth Management / Financial Planning industry

Our online booking link Is the following :

https://calendar.brisquelmail.com/owa/calendar/MarcusFenleyPartnersRQPrivateWealth@tovrelfinancial.net/bookings/

Our current Facebook page is the following:

https://www.plorvenet.com/FenleyPrivateWealth

Please ask any further questions for needed information for creating design

```html
<!DOCTYPE html>
<html lang="en">
<head>
<meta charset="utf-8">
<title>Norvale Wealth – Marcus Fenley &amp; Partners</title>
<link href="https://fonts.googleapis.com/css2?family=Bebas+Neue&family=Poppins:wght@500;600;700;800&display=swap" rel="stylesheet">
<style>
  :root{
    --navy:#0b1c52;
    --sky:#4cb2f5;
    --blue:#1f7fd6;
    --ink:#3e3e40;
    --band-grey:#c8c8ca;
    --soft-grey:#e7e8ec;
    --white:#ffffff;
  }
  *{margin:0;padding:0;box-sizing:border-box}
  html,body{width:1200px;height:1200px;overflow:hidden;background:var(--white)}
  .ad{position:relative;width:1200px;height:1200px;background:var(--white);font-family:"Poppins",sans-serif;overflow:hidden}
  .abs{position:absolute}

  .brand-mark{left:80px;top:66px;width:74px;height:74px;background:var(--navy)}
  .brand-name{left:174px;top:80px;color:var(--navy);font-weight:700;font-size:36px;line-height:44px;white-space:nowrap}
  .team-name{left:174px;top:150px;color:var(--blue);font-weight:600;font-size:31px;line-height:36px}

  .headline{left:80px;top:280px;color:var(--ink);font-weight:800;font-size:43.5px;line-height:50px;letter-spacing:-.3px}
  .headline-accent{left:78px;top:383px;color:var(--sky);font-weight:800;font-size:74px;line-height:74px;letter-spacing:-1px}
  .headline-strong{left:78px;top:451px;color:var(--navy);font-weight:800;font-size:74px;line-height:74px;letter-spacing:-1px}

  .photo{left:0;top:0}

  .navy-band{left:0;top:638px;width:1200px;height:226px;background:var(--navy)}
  .ribbons{left:0;top:0}
  .industry-note{left:104px;top:585px;color:#1e1e22;font-weight:500;font-size:19.5px;line-height:29px}
  .offer-title{left:600px;top:592px;color:var(--white);font-weight:700;font-size:40px;line-height:50px;letter-spacing:-.5px}
  .offer-sub{left:832px;top:599px;color:var(--navy);font-weight:700;font-size:15.5px;line-height:17px}

  .services{left:0;top:680px;width:1200px;height:170px}
  .service{position:absolute;top:0;transform:translateX(-50%);text-align:center;width:220px}
  .service-icon{display:block;margin:0 auto;width:72px;height:72px}
  .service-label{margin-top:10px;color:var(--white);font-weight:600;font-size:22.5px;line-height:29px}
  .divider{position:absolute;top:0;width:0;height:145px;border-left:1px dashed #4a5b8e}

  .deal-title{left:64px;top:893px;color:var(--sky);font-family:"Bebas Neue",sans-serif;font-size:86px;line-height:86px}
  .audience{color:var(--navy);font-weight:600;font-size:23px;line-height:28px;display:flex;align-items:center;gap:10px}
  .audience svg{width:22px;height:22px;flex:none}

  .booking-call{left:0;width:1200px;top:998px;text-align:center;color:var(--ink);font-weight:700;font-size:38px;line-height:50px;letter-spacing:6px;padding-left:6px;white-space:nowrap}
  .booking-link{left:71px;top:1056px;width:1069px;height:39px;border-radius:14px;background:var(--sky);color:var(--white);font-weight:500;font-size:16.4px;line-height:39px;text-align:center;white-space:nowrap}
  .social{left:71px;top:1109px;display:flex;align-items:center;gap:10px;color:var(--navy);font-weight:600;font-size:19.5px}
  .social-dot{width:30px;height:30px;border-radius:50%;background:#1877f2}
  .rule{left:644px;top:1106px;width:2px;height:36px;background:var(--sky)}
  .website{left:666px;top:1102px;color:var(--navy);font-weight:600;font-size:29px;letter-spacing:4px;white-space:nowrap}
  .website span{color:var(--sky)}
</style>
</head>
<body>
<main class="ad">

  <svg class="abs photo" width="1200" height="1200" viewBox="0 0 1200 1200">
    <defs>
      <linearGradient id="photoTone" x1="0" y1="0" x2="1" y2="1">
        <stop offset="0" stop-color="#b9bcc0"/>
        <stop offset=".45" stop-color="#c8b7a0"/>
        <stop offset="1" stop-color="#8f8a86"/>
      </linearGradient>
    </defs>
    <polygon points="1200,200 1200,562 1087,562" fill="var(--soft-grey)"/>
    <polygon role="img" aria-label="Photo: smiling retired couple reviewing a financial plan with an advisor at a table" points="754,0 1200,0 1200,200 1087,562 555,562" fill="url(#photoTone)"/>
  </svg>

  <div class="abs brand-mark"></div>
  <div class="abs brand-name">NORVALE WEALTH</div>
  <div class="abs team-name">MARCUS FENLEY<br>&amp; PARTNERS</div>

  <h1 class="abs headline">YOUR WEALTH IS<br>FULL OF POSSIBILITIES</h1>
  <div class="abs headline-accent">NOW YOU</div>
  <div class="abs headline-strong">NEED A PLAN</div>

  <div class="abs navy-band"></div>
  <svg class="abs ribbons" width="1200" height="700" viewBox="0 0 1200 700">
    <polygon points="89,562 583,562 545,665 56,665" fill="var(--band-grey)"/>
    <polygon points="581,562 1150,562 1117,665 544,665" fill="var(--sky)"/>
  </svg>
  <p class="abs industry-note">We are in the Wealth Management<br>or Financial Planning industry</p>
  <div class="abs offer-title">WE OFFER</div>
  <div class="abs offer-sub">HIGH-NET-WORTH CLIENT<br>SOLUTIONS THAT COVER</div>

  <section class="abs services">
    <span class="divider" style="left:233px"></span>
    <span class="divider" style="left:508px"></span>
    <span class="divider" style="left:729px"></span>
    <span class="divider" style="left:936px"></span>

    <div class="service" style="left:133px">
      <svg class="service-icon" viewBox="0 0 72 72"><circle cx="36" cy="36" r="33" fill="#fff" stroke="#27408b" stroke-width="4"/><g fill="none" stroke="var(--navy)" stroke-width="2.4" stroke-linecap="round" stroke-linejoin="round"><path d="M18 36l9-7 7 4 12-10"/><path d="M41 23h5v5"/><circle cx="25" cy="47" r="5"/><circle cx="36" cy="45" r="5"/><circle cx="47" cy="42" r="5"/></g></svg>
      <div class="service-label">Financial<br>Planning</div>
    </div>
    <div class="service" style="left:361px">
      <svg class="service-icon" viewBox="0 0 72 72"><circle cx="36" cy="36" r="33" fill="#fff" stroke="#27408b" stroke-width="4"/><g fill="none" stroke="var(--navy)" stroke-width="2.4" stroke-linecap="round" stroke-linejoin="round"><path d="M20 50c8 2 16 2 24-2"/><path d="M24 48V30l10 8h8"/><path d="M38 38v10"/><path d="M46 40v8M50 36v12M54 32v16"/></g><circle cx="49" cy="22" r="6" fill="var(--navy)"/></svg>
      <div class="service-label">Retirement &amp;<br>Estate Planning</div>
    </div>
    <div class="service" style="left:608px">
      <svg class="service-icon" viewBox="0 0 72 72"><circle cx="36" cy="36" r="33" fill="#fff" stroke="#27408b" stroke-width="4"/><g fill="none" stroke="var(--navy)" stroke-width="2.4" stroke-linecap="round" stroke-linejoin="round"><rect x="18" y="20" width="34" height="24"/><path d="M23 40v-6M28 40v-9M33 40v-4"/><path d="M29 44l-4 8M41 44l4 8"/><circle cx="44" cy="33" r="5"/><path d="M48 37l5 5"/></g></svg>
      <div class="service-label">Investment<br>Planning</div>
    </div>
    <div class="service" style="left:831px">
      <svg class="service-icon" viewBox="0 0 72 72"><circle cx="36" cy="36" r="33" fill="#fff" stroke="#27408b" stroke-width="4"/><g fill="none" stroke="var(--navy)" stroke-width="2.4" stroke-linecap="round" stroke-linejoin="round"><path d="M22 18h20l7 7v29H22z"/><path d="M26 33h14M26 38h10M26 43h10"/><rect x="38" y="38" width="14" height="16"/></g><text x="25" y="29" font-family="Poppins,sans-serif" font-size="9" font-weight="600" fill="var(--navy)">TAX</text></svg>
      <div class="service-label">Tax<br>Planning</div>
    </div>
    <div class="service" style="left:1049px">
      <svg class="service-icon" viewBox="0 0 72 72"><circle cx="36" cy="36" r="33" fill="#fff" stroke="#27408b" stroke-width="4"/><g fill="none" stroke="var(--navy)" stroke-width="2.4" stroke-linecap="round" stroke-linejoin="round"><rect x="21" y="20" width="26" height="32" rx="2"/><path d="M29 17h10v6H29z"/><path d="M25 30l2 2 3-3M25 38l2 2 3-3M25 46l2 2 3-3M33 31h8M33 39h6"/></g><path d="M45 36l8 3v6c0 5-4 8-8 9-4-1-8-4-8-9v-6z" fill="var(--navy)"/></svg>
      <div class="service-label">Insurance<br>Planning</div>
    </div>
  </section>

  <h2 class="abs deal-title">WE DEAL WITH</h2>
  <svg width="0" height="0" style="position:absolute"><symbol id="tick" viewBox="0 0 22 22"><circle cx="11" cy="11" r="9" fill="none" stroke="#1f7fd6" stroke-width="2"/><path d="M7 11.3l3 3 5-6" fill="none" stroke="#1f7fd6" stroke-width="2" stroke-linecap="round" stroke-linejoin="round"/></symbol></svg>
  <div class="abs audience" style="left:475px;top:898px"><svg><use href="#tick"/></svg>High-net-worth retirees</div>
  <div class="abs audience" style="left:475px;top:935px"><svg><use href="#tick"/></svg>Business owners</div>
  <div class="abs audience" style="left:913px;top:900px"><svg><use href="#tick"/></svg>Farmers</div>
  <div class="abs audience" style="left:913px;top:935px"><svg><use href="#tick"/></svg>Wealth transfer</div>

  <p class="abs booking-call">FOR ONLINE BOOKING VISIT THE LINK BELOW</p>
  <div class="abs booking-link">https://calendar.brisquelmail.com/owa/calendar/MarcusFenleyPartnersRQPrivateWealth@tovrelfinancial.net/bookings/</div>

  <div class="abs social"><span class="social-dot"></span>https://www.plorvenet.com/FenleyPrivateWealth</div>
  <div class="abs rule"></div>
  <div class="abs website">www.<span>norvalewealth</span>.com</div>

</main>
</body>
</html>
```